Wordpress Website Update - Elementor

I'm currently using Elementor and would like my site to be updated. A nice facelift to the current pages. We are a small boutique animation service company.
I have a list of similar production houses to use as references and would like the format/style of the site not to feel so corporate and infuse the fun that we bring to working with clients on animated projects.

Additionally, I'd like to add 2 more pages focusing on more portfolio work and Original IP - which is now our primary goal to sell our show ideas. Maybe have a password projected behind an image showcasing the show/ film. Go to our current site to review. www.pebblemoatfilms.com

Animation/ Commercials/ Vorlica/ Quelbar/ Durno/ KVT - Okay with first page being shorter and not as long as well. Have contact us 'above the fold' on options as well.

Animation and Film

• Current 3 pages - additional 2 - we can focus on layout and arrangement with temporary images then swap with real assets when ready.
• site examples: pirtolstudios.com, Mardle House, Fenra Studios, Gorbleck.net, Quillstone Animation, Brindlemop Animation Studios, ZaZe Studios use Varkel Plus as inspiration.

```html
<!DOCTYPE html>
<html lang="en">
<head>
<meta charset="utf-8">
<title>Pebblemoat Films — Animation Studio</title>
<link rel="stylesheet" href="https://fonts.googleapis.com/css2?family=Oswald:wght@400;500&family=Luckiest+Guy&family=Fredoka:wght@500;600&display=swap">
<style>
:root{
  --ink:#0b0b0b;
  --purple:#7348d9;
  --purple-soft:#9a7ee6;
  --red:#e2434b;
  --grey-head:#9a9a9a;
  --grey-circle:#ececec;
  --footer-left:#141414;
  --footer-right:#242424;
  --white:#ffffff;
  --text:#1a1a1a;
}
*{box-sizing:border-box;margin:0;padding:0}
html,body{width:1200px;height:3643px;overflow:hidden;background:var(--white)}
body{position:relative;font-family:"Oswald",sans-serif;color:var(--text)}
.abs{position:absolute}
a{color:inherit;text-decoration:none}

/* nav */
.site-nav{position:absolute;left:0;top:0;width:1200px;height:66px;background:var(--ink);color:var(--white)}
.site-nav .link{position:absolute;top:22px;font-size:16px;font-weight:500;transform:translateX(-50%);letter-spacing:.2px}
.nav-brand{position:absolute;left:599px;top:14px;transform:translateX(-50%);font-family:"Luckiest Guy",sans-serif;font-size:26px;color:var(--purple-soft);letter-spacing:1px;white-space:nowrap}
.social-dot{position:absolute;width:34px;height:34px;border-radius:50%;background:var(--purple)}

/* hero */
.hero-media{position:absolute;left:0;top:66px;width:1200px;height:644px;
  background:linear-gradient(180deg,#c4566a 0%,#8e3a4e 25%,#5a3460 45%,#3c4c9a 65%,#6a7bc4 82%,#c8ccdf 100%)}
.hero-media::after{content:"";position:absolute;inset:0;background:radial-gradient(ellipse at 25% 70%,rgba(225,80,70,.55),transparent 55%),radial-gradient(ellipse at 70% 60%,rgba(60,90,200,.5),transparent 55%)}
.play-btn{position:absolute;left:565px;top:352px;z-index:2}

/* intro band */
.intro-band{position:absolute;left:0;top:710px;width:1200px;height:255px}
.intro-band p{position:absolute;left:160px;top:58px;width:880px;text-align:center;color:var(--white);font-size:19px;line-height:31.5px;text-transform:uppercase}

/* headings */
.section-title{position:absolute;left:0;width:1200px;text-align:center;font-family:"Luckiest Guy",sans-serif;color:var(--grey-head);font-size:66px;letter-spacing:1px;line-height:1}

/* project grid */
.project-grid{position:absolute;left:0;top:1056px;width:1200px;height:666px;display:grid;grid-template-columns:repeat(4,300px);grid-template-rows:repeat(3,222px)}
.project-tile{position:relative;overflow:hidden}
.project-tile span{position:absolute;left:0;right:0;bottom:18px;text-align:center;color:var(--white);font-size:21px;text-transform:uppercase;letter-spacing:-.3px;text-shadow:0 1px 3px rgba(0,0,0,.5)}
.project-tile::before{content:"";position:absolute;left:0;right:0;bottom:0;height:38%;background:linear-gradient(180deg,transparent,rgba(0,0,0,.35))}

.btn{position:absolute;left:547px;width:107px;height:33px;background:var(--purple);color:var(--white);font-size:11px;text-transform:uppercase;display:flex;align-items:center;justify-content:center;letter-spacing:.2px}

/* co-create */
.cta-box{position:absolute;left:109px;top:1912px;width:985px;height:140px;border:3px solid var(--purple-soft);display:flex;align-items:center;justify-content:center;font-size:29px;text-transform:uppercase;color:var(--ink);padding-bottom:12px}

/* reel */
.reel{position:absolute;left:0;top:2205px;width:1200px;height:568px;background:linear-gradient(180deg,#4a4c52 0%,#5b5650 45%,#3e3a37 100%)}
.reel::after{content:"";position:absolute;inset:0;background:radial-gradient(ellipse at 55% 55%,rgba(150,110,70,.45),transparent 55%)}
.reel-tab{position:absolute;left:599px;top:0;width:601px;height:99px;background:var(--white);z-index:2}
.reel-tab span{position:absolute;left:0;right:0;top:22px;text-align:center;color:var(--purple);font-size:30px;text-transform:uppercase}
.reel-tab i{position:absolute;left:152px;width:297px;top:66px;height:2px;background:var(--purple)}
.reel-label{position:absolute;left:260px;top:2236px;font-size:29px;color:#a8a8a8;text-transform:uppercase;z-index:2;border-bottom:2px solid #a8a8a8;line-height:1.25;padding-bottom:2px}
.reel-copy{position:absolute;left:200px;top:2430px;width:800px;text-align:center;color:var(--white);font-size:21px;line-height:31px;text-transform:uppercase;z-index:2}

/* expertise */
.expertise-item{position:absolute;top:2947px;width:198px;margin-left:-99px;text-align:center}
.expertise-item .disc{width:198px;height:198px;border-radius:50%;background:var(--grey-circle);display:flex;align-items:center;justify-content:center}
.expertise-item .motif{width:110px;height:100px;border-radius:40%;background:var(--red)}
.expertise-item.active .disc{background:var(--purple)}
.expertise-item.active .motif{background:var(--white)}
.expertise-item h3{margin-top:24px;font-family:"Fredoka",sans-serif;font-weight:600;font-size:19px;letter-spacing:.6px;color:var(--ink)}
.expertise-item.active h3{color:var(--purple)}

/* footer */
.footer-left{position:absolute;left:0;top:3338px;width:493px;height:305px;background:var(--footer-left)}
.footer-right{position:absolute;left:493px;top:3338px;width:707px;height:305px;background:var(--footer-right)}
.footer-brand{position:absolute;left:0;width:493px;top:3400px;text-align:center;font-family:"Luckiest Guy",sans-serif;font-size:56px;color:var(--purple);letter-spacing:1px;line-height:1}
.footer-brand-sub{position:absolute;left:0;width:493px;top:3470px;text-align:center;font-family:"Luckiest Guy",sans-serif;font-size:20px;color:var(--purple);letter-spacing:13px}
.footer-dot{position:absolute;top:3520px;width:27px;height:27px;border-radius:50%;background:var(--purple)}
.copyright{position:absolute;left:0;width:493px;top:3563px;text-align:center;color:var(--white);font-size:14px;line-height:27px;text-transform:uppercase}
.footer-head{position:absolute;top:3396px;font-family:"Luckiest Guy",sans-serif;color:var(--white);font-size:23px;letter-spacing:1px}
.footer-links{position:absolute;top:3444px;list-style:none;color:var(--white);font-size:11.5px;text-transform:uppercase}
.footer-links li{height:32px}
.contact-row{position:absolute;left:884px;display:flex;gap:12px;color:var(--white);font-size:11.5px;text-transform:uppercase;line-height:22px}
.contact-row .ico{flex:none;width:24px;height:24px;border-radius:50%;background:var(--purple);display:flex;align-items:center;justify-content:center}
</style>
</head>
<body>

<header class="site-nav">
  <a class="link" style="left:236px" href="#">Home</a>
  <a class="link" style="left:325px" href="#">About</a>
  <a class="link" style="left:432px" href="#">Our Projects</a>
  <div class="nav-brand">Pebblemoat Films</div>
  <a class="link" style="left:745px" href="#">News</a>
  <a class="link" style="left:840px" href="#">Contact</a>
  <span class="social-dot" style="left:905px;top:16px" aria-label="Social link"></span>
  <span class="social-dot" style="left:955px;top:16px" aria-label="Social link"></span>
  <span class="social-dot" style="left:1005px;top:16px" aria-label="Social link"></span>
</header>

<section class="hero-media" role="img" aria-label="Showreel still: a field of glowing voxel columns in red, coral and blue"></section>
<svg class="play-btn" width="68" height="68" viewBox="0 0 68 68" aria-label="Play showreel">
  <circle cx="34" cy="34" r="34" fill="#7348d9"/>
  <path d="M26 20 L50 34 L26 48 Z" fill="#fff"/>
</svg>

<section class="intro-band">
  <svg class="abs" style="left:0;top:0" width="1200" height="255" viewBox="0 0 1200 255" preserveAspectRatio="none">
    <path d="M0 0 H1200 V215 L1160 218 L1120 212 L1060 222 L990 214 L930 220 L860 210 L800 222 L740 216 L690 212 L640 222 L580 214 L520 220 L470 213 L410 222 L350 214 L290 218 L240 212 L180 222 L120 214 L60 220 L20 232 L0 240 Z" fill="#7348d9"/>
  </svg>
  <p>Pebblemoat focuses on authentic stories created by passionate and hungry storytellers. We cultivate fresh, new voices that have something to share with the world! Properties to sell, co-produce and eventually direct with the right partners.</p>
</section>

<h2 class="section-title" style="top:1002px">Just a few projects</h2>

<section class="project-grid">
  <div class="project-tile" role="img" aria-label="Savanna scene with giraffes" style="background:linear-gradient(180deg,#5fa6d6,#c9a25a 55%,#7b6a3a)"><span>Arc Experience</span></div>
  <div class="project-tile" role="img" aria-label="Animated puppy character on purple" style="background:linear-gradient(160deg,#6a4cd6,#3a2a9a)"><span>Vis Dev</span></div>
  <div class="project-tile" role="img" aria-label="Costumed mascots at an outdoor event" style="background:linear-gradient(180deg,#7b8a6e,#9aa0a6 55%,#55585e)"><span>Halvern Davos</span></div>
  <div class="project-tile" role="img" aria-label="Mobile game characters in a jungle" style="background:linear-gradient(160deg,#d08a3a,#8a6a4a 55%,#5a4a3a)"><span>Mobile Game Animation</span></div>
  <div class="project-tile" role="img" aria-label="Storyboard frame of children at school" style="background:linear-gradient(180deg,#4a7a9a,#b35a3a 60%,#7a5a4a)"><span>Storyboard Pitch</span></div>
  <div class="project-tile" role="img" aria-label="Animated characters on a stage" style="background:linear-gradient(180deg,#7a5ad6,#4a3a8a)"><span>Halvern Animation</span></div>
  <div class="project-tile" role="img" aria-label="Colourful classroom development art" style="background:linear-gradient(180deg,#d8b04a,#6a9a7a 55%,#5a7ab0)"><span>Visual Development</span></div>
  <div class="project-tile" role="img" aria-label="Puppy character concept for an AR book" style="background:linear-gradient(160deg,#8a6ae0,#4a3aa0)"><span>AR Book Concept</span></div>
  <div class="project-tile" role="img" aria-label="Live action shoot with a costume character" style="background:linear-gradient(180deg,#4a6a3a,#3a3a32)"><span>IP Creation</span></div>
  <div class="project-tile" role="img" aria-label="Animated children playing music" style="background:linear-gradient(160deg,#5ab08a,#6a4ab0 60%,#3a2a6a)"><span>Tremlo Storyboards</span></div>
  <div class="project-tile" role="img" aria-label="Group of animated kids outdoors" style="background:linear-gradient(180deg,#6ab0e0,#a05a7a 60%,#6a4a5a)"><span>Norvell Storyboards</span></div>
  <div class="project-tile" role="img" aria-label="Animated scientist character with a cloud" style="background:linear-gradient(160deg,#3a8ad0,#b0c0cc 60%,#8a8a8a)"><span>Halvern Animation</span></div>
</section>

<a class="btn" style="top:1750px" href="#">Learn More</a>

<h2 class="section-title" style="top:1858px">Why wait let's co-create!</h2>
<div class="cta-box">No need to scroll, save your finger and drop us a line.</div>
<a class="btn" style="top:2086px" href="#">Contact Us</a>

<section class="reel" role="img" aria-label="Commercial still: a painting of an ark with giraffes in a living room"></section>
<div class="reel-tab" style="top:2205px"><span>Giraffes &amp; Kids Are Free!</span><i></i></div>
<div class="reel-label">Animation Reel</div>
<p class="reel-copy">Pebblemoat kicked major butt on this fun project. Read more about the role we played bringing this commercial to life...</p>
<a class="btn" style="top:2509px;z-index:2" href="#">Read More</a>

<h2 class="section-title" style="top:2848px">Our Expertise</h2>
<div class="expertise-item" style="left:223px"><div class="disc"><div class="motif" role="img" aria-label="Red monster character icon"></div></div><h3>IP CREATION</h3></div>
<div class="expertise-item" style="left:478px"><div class="disc"><div class="motif" role="img" aria-label="Open storybook with a character icon"></div></div><h3>STORY</h3></div>
<div class="expertise-item active" style="left:732px"><div class="disc"><div class="motif" role="img" aria-label="Laughing character face icon"></div></div><h3>ANIMATION</h3></div>
<div class="expertise-item" style="left:987px"><div class="disc"><div class="motif" role="img" aria-label="Rigged creature character icon"></div></div><h3>3D RIGGING</h3></div>
<a class="btn" style="top:3218px" href="#">See More &#8964;</a>

<footer>
  <div class="footer-left"></div>
  <div class="footer-right"></div>
  <div class="footer-brand">Pebblemoat</div>
  <div class="footer-brand-sub">FILMS</div>
  <span class="footer-dot" style="left:203px" aria-label="Social link"></span>
  <span class="footer-dot" style="left:247px" aria-label="Social link"></span>
  <span class="footer-dot" style="left:291px" aria-label="Social link"></span>
  <span class="footer-dot" style="left:335px" aria-label="Social link"></span>
  <p class="copyright">©Copyrights 2022 Pebblemoatfilms<br>All rights reserved</p>

  <h4 class="footer-head" style="left:565px">Quick Links</h4>
  <ul class="footer-links" style="left:566px">
    <li>Home</li><li>About</li><li>Our Projects</li><li>News</li><li>Contact</li>
  </ul>
  <ul class="footer-links" style="left:732px">
    <li>Terms</li><li>Conditions</li><li>Privacy Policy</li><li>Support</li><li>Blog</li>
  </ul>

  <h4 class="footer-head" style="left:893px">Contact Us</h4>
  <div class="contact-row" style="top:3446px">
    <span class="ico"><svg width="12" height="14" viewBox="0 0 12 14"><path d="M6 0a5 5 0 0 0-5 5c0 4 5 9 5 9s5-5 5-9a5 5 0 0 0-5-5z" fill="#fff"/><circle cx="6" cy="5" r="2" fill="#7348d9"/></svg></span>
    <span>2003 Lorem ipsum dolosit<br>amet0612</span>
  </div>
  <div class="contact-row" style="top:3497px">
    <span class="ico"><svg width="13" height="10" viewBox="0 0 13 10"><rect x=".5" y=".5" width="12" height="9" fill="none" stroke="#fff"/><path d="M.5 .5 6.5 5.5 12.5 .5" fill="none" stroke="#fff"/></svg></span>
    <span>info@pebblemoatfilms.com</span>
  </div>
  <div class="contact-row" style="top:3542px">
    <span class="ico"><svg width="12" height="14" viewBox="0 0 12 14"><path d="M6 0a5 5 0 0 0-5 5c0 4 5 9 5 9s5-5 5-9a5 5 0 0 0-5-5z" fill="#fff"/><circle cx="6" cy="5" r="2" fill="#7348d9"/></svg></span>
    <span>+1 555 010 0199</span>
  </div>
</footer>

</body>
</html>
```